Business Card Design for Marketing Firm

Looking for business card design for higher end marketing firm. Clean but impressionable/trendy. We are a marketing firm that represents manufacturers in the foodservice equipment and supply industry. Our customers are end users such has hotels, restaurants, country clubs, convention centers and casinos as well as distributors of restaurants supplies and equipment, and manufacturers of foodservice equipment and supplies.
Target Market(s)
Hotels, Restaurants, Supply & Equipment Distributors, Foodservice Manufacturers
Industry/Entity Type
Foodservice/Hospitality
Contact Information for Business Card
Name, Title, Contact Number, Email, Website, Social Media, Address
Requirements
Must have
- Clean & Simple but Serious and Impressionable

```html
<!DOCTYPE html>
<html lang="en">
<head>
<meta charset="utf-8">
<title>Meridian Service Reps – Business Card</title>
<link href="https://fonts.googleapis.com/css2?family=Montserrat:wght@400;500;600;700&display=swap" rel="stylesheet">
<style>
  :root {
    --navy: #2c2e67;
    --navy-deep: #25275a;
    --white: #ffffff;
    --grey-band: #b9b9bb;
    --ink: #333333;
    --backdrop: #e9e7e3;
  }
  * { margin: 0; padding: 0; box-sizing: border-box; }
  html, body { width: 900px; height: 1200px; overflow: hidden; }
  body {
    background: var(--backdrop);
    font-family: 'Montserrat', Arial, sans-serif;
    position: relative;
  }
  .card {
    position: absolute;
    left: 80px;
    width: 742px;
    height: 442px;
    border-radius: 32px;
    overflow: hidden;
    box-shadow: 0 6px 10px rgba(0,0,0,0.35);
  }
  .card--front { top: 130px; background: var(--white); }
  .card--back { top: 638px; height: 440px; background: var(--navy); }

  .brand-mark {
    position: absolute;
    left: 0; right: 0;
    display: flex;
    flex-direction: column;
    align-items: center;
    gap: 18px;
  }
  .brand-mark__dot {
    width: 46px; height: 46px;
    border-radius: 50%;
  }
  .brand-mark__name {
    font-weight: 600;
    letter-spacing: 1.5px;
    text-transform: uppercase;
    text-align: center;
  }
  .card--front .brand-mark { top: 100px; left: -46px; }
  .card--front .brand-mark__dot { background: var(--navy); }
  .card--front .brand-mark__name { color: var(--navy); font-size: 27px; }
  .card--back .brand-mark { top: 140px; }
  .card--back .brand-mark__dot { background: var(--white); width: 56px; height: 56px; }
  .card--back .brand-mark__name { color: var(--white); font-size: 33px; }

  .person {
    position: absolute;
    right: 44px;
    top: 282px;
    text-align: right;
  }
  .person__name {
    font-size: 26px;
    font-weight: 600;
    color: var(--navy);
    line-height: 1.1;
  }
  .person__title {
    font-size: 15.5px;
    color: var(--ink);
    margin-top: 6px;
    letter-spacing: 0.3px;
  }
  .divider {
    position: absolute;
    left: 42px;
    top: 326px;
    width: 506px;
    height: 1.5px;
    background: var(--navy);
  }
  .contact-list {
    position: absolute;
    left: 38px;
    top: 342px;
    list-style: none;
  }
  .contact-list li {
    display: flex;
    align-items: center;
    gap: 12px;
    font-size: 15.5px;
    color: var(--ink);
    height: 24px;
  }
  .contact-list svg { width: 14px; height: 14px; fill: var(--navy); }
  .footer-bands {
    position: absolute;
    left: 0; bottom: 0;
    width: 742px; height: 42px;
  }
  .address {
    position: absolute;
    right: 30px;
    bottom: 8px;
    color: var(--white);
    font-size: 15.5px;
  }
</style>
</head>
<body>
  <section class="card card--front">
    <div class="brand-mark">
      <span class="brand-mark__dot"></span>
      <span class="brand-mark__name">Meridian Service Reps</span>
    </div>

    <div class="person">
      <p class="person__name">Daniel Reyes</p>
      <p class="person__title">CEO &amp; Founder</p>
    </div>
    <div class="divider"></div>

    <ul class="contact-list">
      <li>
        <svg viewBox="0 0 24 24"><path d="M6.6 10.8a15.1 15.1 0 0 0 6.6 6.6l2.2-2.2a1 1 0 0 1 1-.25 11.4 11.4 0 0 0 3.6.57 1 1 0 0 1 1 1V20a1 1 0 0 1-1 1A17 17 0 0 1 3 4a1 1 0 0 1 1-1h3.5a1 1 0 0 1 1 1c0 1.25.2 2.45.57 3.6a1 1 0 0 1-.25 1z"/></svg>
        (555) 014-2870
      </li>
      <li>
        <svg viewBox="0 0 24 24"><path d="M2 5h20v2l-10 6L2 7z M2 9l10 6 10-6v10H2z"/></svg>
        info@meridianservicereps.com
      </li>
      <li>
        <svg viewBox="0 0 24 24"><circle cx="12" cy="12" r="10"/></svg>
        www.meridianservicereps.com
      </li>
    </ul>

    <svg class="footer-bands" viewBox="0 0 742 42" preserveAspectRatio="none">
      <polygon points="0,27 316,27 300,42 0,42" fill="var(--grey-band)"/>
      <polygon points="352,2 742,2 742,42 318,42" fill="var(--navy)"/>
    </svg>
    <p class="address">420 Harbor Lane, Suite 900, Bayview, CA 90210</p>
  </section>

  <section class="card card--back">
    <div class="brand-mark">
      <span class="brand-mark__dot"></span>
      <span class="brand-mark__name">Meridian Service Reps</span>
    </div>
  </section>
</body>
</html>
```